IT Product Event Invitations

We are requesting the design of two invitations for a series of technological events that will be held between the company Tidewell Labs and its partner in the Dominican Republic, Corvantel.
Both events represent the launch of the Tidewell Labs brand in the Dominican Republic.
The first event is an elegant dinner aimed at the banking sector of the Dominican Republic to showcase the "Ledgerline Banking Suite" software.
Event information:
- Descriptive text for the invitation: Corvantel y Tidewell Labs le invitan a descubrir cómo reducir costos, aumentar la automatización y mejorar la satisfacción de los clientes a través de una solución única para enfrentar los desafíos de la banca.
- Date: 25 de Septiembre
- Time: 7PM
- Location: El Pimiento, Av. Julián Marcano 318
In the invitation, consider using the colors of the Tidewell Labs and Corvantel brands if possible. You can find the logos in the webpage
The second event is a wine tasting to present "Harborview Operations Hub" aimed at various industries.
Event information:
- Descriptive text for the invitation: Corvantel y Tidewell Labs le invitan a conocer una solución que le permitirá a toda su empresa brindar una experiencia de servicio a otro nivel.
- Date: 26 de Septiembre
- Time: 7PM
In the invitation, consider using the colors of the Tidewell Labs and Corvantel brands if possible. You can find the logos in the web page.
Both invitations must have a button for participant registration and that when you click on the image, it will direct you to a form.
Form for Ledgerline Banking Suite: https://signup.corvantel-events.example/ledgerline-dinner
Form for Harborview Operations Hub: https://signup.corvantel-events.example/harborview-tasting
Target Market(s)
Enterprise Customers
Industry/Entity Type
Technology
Look and feel
Each slider illustrates characteristics of the customer's brand and the style your logo design should communicate.

```html
<!DOCTYPE html>
<html lang="es">
<head>
<meta charset="utf-8">
<title>Tidewell Labs × Corvantel — Invitaciones</title>
<link rel="stylesheet" href="https://fonts.googleapis.com/css2?family=Archivo:wdth,wght@125,800;125,900&family=Poppins:wght@400;500;700&display=swap">
<style>
  :root {
    --stage: #a3a3a3;
    --navy-deep: #141d3f;
    --navy: #1b2a6b;
    --blue-glow: #1f63c8;
    --cyan: #3fb8e8;
    --frame: #ffffff;
    --green: #6ccf3c;
    --text: #ffffff;
    --button: #1f74d4;
    --button-edge: #8fd4ff;
  }
  * { box-sizing: border-box; margin: 0; padding: 0; }
  html, body { width: 828px; height: 1200px; overflow: hidden; }
  body {
    background: var(--stage);
    display: flex;
    align-items: center;
    justify-content: center;
    gap: 24px;
    font-family: "Poppins", sans-serif;
    color: var(--text);
  }
  .invitation {
    position: relative;
    width: 372px;
    height: 517px;
    overflow: hidden;
    text-align: center;
  }
  .invitation__backdrop {
    position: absolute;
    inset: 0;
    background:
      radial-gradient(ellipse 70% 30% at 50% 88%, rgba(47,140,230,.55), transparent 70%),
      radial-gradient(ellipse 60% 25% at 40% 8%, rgba(50,130,220,.45), transparent 70%),
      linear-gradient(180deg, var(--navy) 0%, #1a2660 45%, var(--navy-deep) 70%, #172a66 100%);
  }
  .invitation__frame {
    position: absolute;
    inset: 17px;
    border: 2px solid var(--frame);
  }
  .invitation__frame::after {
    content: "";
    position: absolute;
    inset: 6px;
    border: 1px solid var(--cyan);
    opacity: .8;
  }
  .invitation__content {
    position: relative;
    padding: 48px 30px 0;
  }
  .brand-row {
    display: flex;
    align-items: center;
    justify-content: center;
    gap: 10px;
    font-weight: 500;
    font-size: 14px;
    letter-spacing: .2px;
  }
  .brand-row__divider {
    width: 1px;
    height: 16px;
    background: var(--text);
  }
  .event-title {
    margin-top: 22px;
    font-family: "Archivo", sans-serif;
    font-stretch: 125%;
    font-weight: 900;
    line-height: .92;
    letter-spacing: -.5px;
  }
  .event-title span { display: block; }
  .event-title__line { font-size: 30px; }
  .event-title__accent { color: var(--green); font-size: 31px; }
  .event-description {
    margin: 24px auto 0;
    max-width: 290px;
    font-size: 9.4px;
    line-height: 1.3;
  }
  .event-details {
    margin: 22px auto 0;
    width: 288px;
    height: 48px;
    display: flex;
    border-top: 1.2px solid var(--text);
    border-bottom: 1.2px solid var(--text);
  }
  .event-details__when {
    width: 122px;
    border-right: 1.2px solid var(--text);
    display: flex;
    flex-direction: column;
    justify-content: center;
  }
  .event-details__date { font-size: 10px; line-height: 1.2; }
  .event-details__time {
    font-family: "Archivo", sans-serif;
    font-weight: 800;
    font-size: 22px;
    line-height: 1;
  }
  .event-details__where {
    flex: 1;
    display: flex;
    align-items: center;
    gap: 6px;
    padding-left: 14px;
    text-align: left;
    font-size: 9.6px;
    line-height: 1.25;
    letter-spacing: .3px;
  }
  .event-details__pin { width: 12px; height: 16px; flex: none; }
  .register-button {
    display: inline-block;
    margin-top: 22px;
    padding: 4px 12px;
    border-radius: 16px;
    border: 1.5px solid var(--button-edge);
    background: linear-gradient(180deg, #2c8ae6, var(--button));
    color: var(--text);
    text-decoration: none;
    font-weight: 700;
    font-size: 14px;
    letter-spacing: .3px;
    box-shadow: 0 0 0 1px rgba(20,60,140,.6), 0 0 10px rgba(63,184,232,.4);
  }
</style>
</head>
<body>

  <article class="invitation">
    <div class="invitation__backdrop" role="img" aria-label="Fondo tecnológico azul con formas geométricas luminosas"></div>
    <div class="invitation__frame"></div>
    <div class="invitation__content">
      <div class="brand-row">
        <span>Tidewell Labs</span>
        <span class="brand-row__divider"></span>
        <span>Corvantel</span>
      </div>
      <h1 class="event-title">
        <span class="event-title__line">Ledgerline</span>
        <span class="event-title__line">Banking</span>
        <span class="event-title__accent">Suite</span>
      </h1>
      <p class="event-description">Corvantel y Tidewell Labs le invitan a descubrir cómo reducir costos, aumentar la automatización y mejorar la satisfacción de los clientes a través de una solución única para enfrentar los desafíos de la banca.</p>
      <div class="event-details">
        <div class="event-details__when">
          <span class="event-details__date">25 de Septiembre</span>
          <span class="event-details__time">7PM</span>
        </div>
        <div class="event-details__where">
          <svg class="event-details__pin" viewBox="0 0 12 16" aria-hidden="true">
            <path d="M6 1a5 5 0 0 0-5 5c0 3.6 5 9 5 9s5-5.4 5-9a5 5 0 0 0-5-5z" fill="none" stroke="#6ccf3c" stroke-width="2"/>
            <circle cx="6" cy="6" r="1.8" fill="#6ccf3c"/>
          </svg>
          <span>El Pimiento, Av. Julián<br>Marcano 318</span>
        </div>
      </div>
      <a class="register-button" href="https://signup.corvantel-events.example/ledgerline-dinner">REGISTER HERE</a>
    </div>
  </article>

  <article class="invitation">
    <div class="invitation__backdrop" role="img" aria-label="Fondo tecnológico azul con formas geométricas luminosas"></div>
    <div class="invitation__frame"></div>
    <div class="invitation__content">
      <div class="brand-row">
        <span>Tidewell Labs</span>
        <span class="brand-row__divider"></span>
        <span>Corvantel</span>
      </div>
      <h1 class="event-title">
        <span class="event-title__line">Harborview</span>
        <span class="event-title__line">Operations</span>
        <span class="event-title__accent">Hub</span>
      </h1>
      <p class="event-description">Corvantel y Tidewell Labs le invitan a conocer una solución que le permitirá a toda su empresa brindar una experiencia de servicio a otro nivel.</p>
      <div class="event-details">
        <div class="event-details__when">
          <span class="event-details__date">26 de Septiembre</span>
          <span class="event-details__time">7PM</span>
        </div>
        <div class="event-details__where">
          <svg class="event-details__pin" viewBox="0 0 12 16" aria-hidden="true">
            <path d="M6 1a5 5 0 0 0-5 5c0 3.6 5 9 5 9s5-5.4 5-9a5 5 0 0 0-5-5z" fill="none" stroke="#6ccf3c" stroke-width="2"/>
            <circle cx="6" cy="6" r="1.8" fill="#6ccf3c"/>
          </svg>
          <span>El Pimiento, Av. Julián<br>Marcano 318</span>
        </div>
      </div>
      <a class="register-button" href="https://signup.corvantel-events.example/harborview-tasting">REGISTER HERE</a>
    </div>
  </article>

</body>
</html>
```